Need Web Design for Business Process Outsourcing Company (Quorvane)

Quorvane is a business process outsourcing company. Need a simple site similar to http://www.tallowbrinkhire.com/ but with a more professional and credible look. New to the process; not sure where to start and comparing my options. Please let me know what my options are if I choose to go with you. Logo is attached for your reference. Please use same colorway

Reason: I want the final product to be coded. Please confirm you will be able to code final design.

Industry/Entity Type

Business

Coding

Coded - Design and coding required

```html
<!DOCTYPE html>
<html lang="en">
<head>
<meta charset="utf-8">
<title>Quorvane Services</title>
<link href="https://fonts.googleapis.com/css2?family=Lato:wght@400;700&family=Roboto:wght@400;500&display=swap" rel="stylesheet">
<style>
:root{
  --blue:#0b8fd6;
  --navy:#0c5590;
  --deep:#07457a;
  --ink:#333;
  --grey:#777;
  --light:#eeeeee;
  --pale:#e6f0f7;
  --white:#fff;
}
*{margin:0;padding:0;box-sizing:border-box}
html,body{width:1200px;height:3255px;overflow:hidden}
body{position:relative;font-family:Arial,Helvetica,sans-serif;color:var(--ink);background:var(--white)}
section,header,footer{position:absolute;left:0;width:1200px}
.abs{position:absolute}
.brand{font-family:'Roboto',sans-serif;font-weight:500;display:flex;align-items:center;gap:12px}
.brand-mark{width:40px;height:40px;background:var(--blue)}
/* header */
.site-header{top:0;height:100px;background:var(--white)}
.site-header .brand{left:76px;top:28px;font-size:34px;color:var(--navy)}
.main-nav{position:absolute;right:76px;top:32px;display:flex;gap:0;font-family:'Roboto',sans-serif;font-size:17px}
.main-nav a{color:#444;text-decoration:none;padding:10px 12px}
.main-nav a.active{background:var(--blue);color:var(--white);padding:10px 16px;margin-right:8px}
/* hero */
.hero{top:100px;height:578px;background:linear-gradient(160deg,#5d6b78 0%,#3a4f66 45%,#243b56 100%)}
.hero-photo{position:absolute;inset:0}
.hero h1{position:absolute;top:180px;left:0;width:1200px;text-align:center;font-family:'Lato',sans-serif;font-weight:700;font-size:50px;line-height:58px;color:var(--white)}
.hero p{position:absolute;top:310px;left:175px;width:850px;text-align:center;font-size:16px;line-height:24px;color:#111}
.btn{display:inline-block;background:var(--blue);color:var(--white);font-family:'Roboto',sans-serif;font-size:19px;text-align:center;text-decoration:none}
.hero .btn{position:absolute;left:478px;top:366px;width:245px;height:58px;line-height:58px;border:1px solid #3fb0ee}
.slide-arrow{position:absolute;top:255px;width:50px;height:50px;border:2px solid #222;border-radius:50%}
/* welcome */
.welcome{top:678px;height:229px;background:var(--navy);color:var(--white);text-align:center}
.welcome h2{margin-top:40px;font-family:'Roboto',sans-serif;font-weight:400;font-size:42px}
.welcome p{width:960px;margin:14px auto 0;font-size:14px;line-height:26px;color:#dce9f4}
.chev{display:block;margin:6px auto 0}
/* services */
.services{top:907px;height:710px;background:var(--white)}
.services-deco{position:absolute;left:240px;top:0;width:720px;height:710px;background:var(--pale);border-radius:60px;opacity:.7}
.section-title{font-family:'Roboto',sans-serif;font-weight:400;font-size:42px;color:var(--navy);text-align:center}
.services .section-title{position:absolute;top:55px;width:1200px}
.svc-label{position:absolute;font-family:'Roboto',sans-serif;font-size:19px;color:var(--navy)}
.svc-text{position:absolute;width:244px;font-size:14px;line-height:24.5px;color:var(--grey)}
.right{text-align:right}
.services svg.hub{position:absolute;left:0;top:0}
/* band */
.pillars{top:1617px;height:363px;background:linear-gradient(180deg,#0b4f8a 0%,#0a5ea0 60%,#073f70 100%)}
.pillar{position:absolute;top:60px;width:250px;text-align:center;color:var(--white)}
.pillar svg{display:block;margin:0 auto;height:80px}
.pillar h3{margin-top:20px;font-family:'Roboto',sans-serif;font-weight:400;font-size:21px;white-space:nowrap}
.pillar p{margin-top:10px;font-size:14px;line-height:24px;color:#dbe8f3}
/* news */
.news{top:1980px;height:578px}
.news .section-title{margin-top:60px}
.card{position:absolute;top:123px;width:332px}
.card-photo{height:208px;background:linear-gradient(135deg,#c9d6e0,#6f8597)}
.card h3{margin-top:22px;font-family:'Roboto',sans-serif;font-weight:500;font-size:21px;color:var(--navy)}
.card .date{margin-top:8px;font-size:16px;color:var(--navy);display:flex;align-items:center;gap:8px}
.card p{margin-top:6px;font-size:13.5px;line-height:23px;color:var(--grey)}
.card .more{display:block;margin-top:4px;font-family:'Roboto',sans-serif;font-weight:500;font-size:14px;color:var(--navy);text-decoration:none}
/* cta */
.cta{top:2558px;height:354px;background:var(--light);text-align:center}
.cta h2{width:900px;margin:64px auto 0;font-family:'Roboto',sans-serif;font-weight:400;font-size:34px;line-height:48px;color:var(--navy)}
.cta p{width:960px;margin:20px auto 0;font-size:14px;line-height:26px;color:var(--grey)}
.cta .btn{margin-top:22px;width:176px;height:56px;line-height:56px}
/* footer */
.site-footer{top:2912px;height:282px;background:var(--navy);color:#dce9f4}
.col{position:absolute;top:42px;width:250px}
.col h4{font-family:'Roboto',sans-serif;font-weight:500;font-size:18px;color:var(--white);margin-bottom:14px}
.site-footer .brand{font-size:36px;color:var(--white)}
.site-footer .brand .brand-mark{background:var(--white)}
.col p{font-size:14px;line-height:24px}
.socials{display:flex;gap:14px;margin-top:30px}
.socials span{width:46px;height:46px;border:1px solid #4c8fc4;border-radius:50%}
.socials span:first-child{background:var(--blue);border-color:var(--blue)}
.links li{list-style:none;font-size:14px;line-height:23px;display:flex;align-items:center;gap:14px}
.links li::before{content:"";width:8px;height:8px;border:1px solid #6fa7d4}
.links li:first-child::before{background:var(--blue);border-color:var(--blue);border-radius:50%}
.contact-item{display:flex;gap:18px;font-size:14px;line-height:24px;margin-bottom:16px}
.contact-item svg{flex:none;margin-top:4px}
.signup input{display:block;width:247px;height:40px;border:0;padding:0 8px;font-size:13px;margin-top:14px;background:#f3f3f3}
.signup .btn{display:block;width:154px;height:40px;line-height:40px;margin-top:10px;font-size:18px}
.copyright{top:3194px;height:61px;background:#0b68ac;text-align:center;line-height:61px;font-size:14px;color:var(--white)}
.copyright b{font-weight:400;color:#7fd0ff}
</style>
</head>
<body>

<header class="site-header">
  <div class="brand abs"><span class="brand-mark"></span>Quorvane</div>
  <nav class="main-nav">
    <a class="active">HOME</a><a>ABOUT</a><a>SERVICES</a><a>STRATEGY</a><a>EXPERIENCY</a><a>SECURITY</a><a>NEWS</a><a>CONTACT</a>
  </nav>
</header>

<section class="hero">
  <div class="hero-photo" role="img" aria-label="Office desk with laptop overlaid by digital data graphics"></div>
  <h1>SEE WHAT QUORVANE SERVICES<br>OUTSOURCING</h1>
  <p>Lorem Ipsum is simply dummy text of the printing and typesetting industry. Lorem Ipsum has been the industry's standard dummy text ever since the 1500s, when an unknown</p>
  <a class="btn">CONTACT US KNOW</a>
  <svg class="slide-arrow" style="left:14px" viewBox="0 0 50 50"><path d="M28 17l-8 8 8 8" fill="none" stroke="#222" stroke-width="2"/></svg>
  <svg class="slide-arrow" style="left:1136px" viewBox="0 0 50 50"><path d="M22 17l8 8-8 8" fill="none" stroke="#222" stroke-width="2"/></svg>
</section>

<section class="welcome">
  <h2>WELCOME TO QUORVANE SERVICES</h2>
  <p>Lorem Ipsum is simply dummy text of the printing and typesetting industry. Lorem Ipsum has been the industry's standard dummy text ever since the 1500s, when an unknown printer took a galley of type and scrambled it to make a type specimen book. It has survived not only five centuries, but also the leap into electronic typesetting, remaining essentially unchanged.</p>
  <svg class="chev" width="18" height="16" viewBox="0 0 18 16"><path d="M2 2l7 6 7-6M2 8l7 6 7-6" fill="none" stroke="#4aa9e8" stroke-width="2"/></svg>
</section>

<section class="services">
  <div class="services-deco"></div>
  <h2 class="section-title">OUR SERVICES</h2>
  <div class="svc-label" style="left:0;width:1200px;text-align:center;top:118px">CUSTOMER SERVICE</div>

  <div class="svc-label right" style="left:82px;width:244px;top:290px">ECOMMERCE</div>
  <p class="svc-text right" style="left:82px;top:325px">Lorem Ipsum is simply dummy text of the printing and typesetting industry. Lorem Ipsum has been the industry's standard dummy text</p>
  <div class="svc-label" style="left:872px;top:290px">IT SOLUTIONS</div>
  <p class="svc-text" style="left:872px;top:325px">Lorem Ipsum is simply dummy text of the printing and typesetting industry. Lorem Ipsum has been the industry's standard dummy text</p>
  <div class="svc-label right" style="left:114px;width:244px;top:522px">HUMAN RESOURCES</div>
  <p class="svc-text right" style="left:114px;top:557px">Lorem Ipsum is simply dummy text of the printing and typesetting industry. Lorem Ipsum has been the industry's standard dummy text</p>
  <div class="svc-label" style="left:842px;top:522px">CREATIVE</div>
  <p class="svc-text" style="left:842px;top:557px">Lorem Ipsum is simply dummy text of the printing and typesetting industry. Lorem Ipsum has been the industry's standard dummy text</p>

  <svg class="hub" width="1200" height="710" viewBox="0 0 1200 710">
    <circle cx="599" cy="417" r="218" fill="#cfe6f5"/>
    <circle cx="599" cy="417" r="200" fill="#1593d8"/>
    <text x="599" y="432" text-anchor="middle" font-family="Roboto,sans-serif" font-size="44" font-weight="500" fill="#fff">Quorvane</text>
    <g fill="#0c5590" stroke="#fff" stroke-width="8">
      <circle cx="599" cy="215" r="64"/>
      <circle cx="410" cy="360" r="64"/>
      <circle cx="786" cy="360" r="64"/>
      <circle cx="456" cy="569" r="64"/>
      <circle cx="744" cy="569" r="64"/>
    </g>
    <g fill="none" stroke="#fff" stroke-width="4" stroke-linecap="round" stroke-linejoin="round">
      <circle cx="599" cy="213" r="17"/><path d="M574 215a25 25 0 0 1 50 0M574 212v12M624 212v12M620 228q-6 12-18 12"/>
      <path d="M384 340h10l8 30h28l6-22h-38"/><circle cx="406" cy="380" r="4"/><circle cx="426" cy="380" r="4"/>
      <path d="M776 376h20M778 383h16M776 370q-10-8-10-20a20 20 0 0 1 40 0q0 12-10 20z"/><path d="M786 316v-8M760 328l-6-6M812 328l6-6"/>
      <circle cx="456" cy="552" r="9"/><circle cx="437" cy="558" r="7"/><circle cx="475" cy="558" r="7"/><path d="M440 588v-12a16 16 0 0 1 32 0v12M424 586v-8a12 12 0 0 1 12-10M488 586v-8a12 12 0 0 0-12-10"/>
      <rect x="720" y="545" width="48" height="36"/><path d="M734 581v8M754 581v8M728 589h32M732 553l24 20M756 553l-24 20"/>
    </g>
  </svg>
</section>

<section class="pillars">
  <div class="pillar" style="left:77px">
    <svg viewBox="0 0 100 80" width="100"><g fill="#fff"><circle cx="40" cy="32" r="20"/><circle cx="70" cy="58" r="14"/></g><circle cx="40" cy="32" r="7" fill="#0b56a0"/><circle cx="70" cy="58" r="5" fill="#0b56a0"/></svg>
    <h3>REINVENTING SERVICES</h3>
    <p>Lorem Ipsum is simply dummy text of the printing and typesetting industry. Lorem Ipsum has been the.</p>
  </div>
  <div class="pillar" style="left:337px">
    <svg viewBox="0 0 100 80" width="100"><g fill="#fff"><rect x="22" y="10" width="26" height="70"/><rect x="52" y="30" width="26" height="50"/><rect x="10" y="40" width="10" height="40"/></g></svg>
    <h3>OUR FACILITES</h3>
    <p>Lorem Ipsum is simply dummy text of the printing and typesetting industry. Lorem Ipsum has been the.</p>
  </div>
  <div class="pillar" style="left:608px">
    <svg viewBox="0 0 120 80" width="120"><path d="M8 66l32-20 24 10 40-34" fill="none" stroke="#fff" stroke-width="8"/><path d="M96 16h18v18z" fill="#fff"/></svg>
    <h3>SUCCESS STOIES</h3>
    <p>Lorem Ipsum is simply dummy text of the printing and typesetting industry. Lorem Ipsum has been the.</p>
  </div>
  <div class="pillar" style="left:873px">
    <svg viewBox="0 0 100 80" width="100"><g fill="#fff"><circle cx="50" cy="22" r="12"/><circle cx="26" cy="30" r="9"/><circle cx="74" cy="30" r="9"/><path d="M32 72v-18a18 18 0 0 1 36 0v18z"/><path d="M12 72v-12a14 14 0 0 1 18-12v24zM88 72v-12a14 14 0 0 0-18-12v24z"/></g></svg>
    <h3>OUR PEOPLE</h3>
    <p>Lorem Ipsum is simply dummy text of the printing and typesetting industry. Lorem Ipsum has been the.</p>
  </div>
  <svg class="abs" style="left:0;top:290px" width="1200" height="20" viewBox="0 0 1200 20"><g fill="none" stroke="#4aa9e8" stroke-width="2"><path d="M195 4l7 5 7-5M195 10l7 5 7-5M455 4l7 5 7-5M455 10l7 5 7-5M726 4l7 5 7-5M726 10l7 5 7-5M991 4l7 5 7-5M991 10l7 5 7-5"/></g></svg>
</section>

<section class="news">
  <h2 class="section-title">LATEST NEWS</h2>
  <article class="card" style="left:78px">
    <div class="card-photo" role="img" aria-label="Business people reviewing documents at a desk"></div>
    <h3>QUORVANE SERVICES</h3>
    <div class="date"><svg width="16" height="16" viewBox="0 0 16 16"><rect x="1" y="3" width="14" height="12" fill="none" stroke="#0c5590" stroke-width="2"/><path d="M1 7h14" stroke="#0c5590" stroke-width="2"/></svg>14 Nov 2016</div>
    <p>Lorem Ipsum is simply dummy text of the print ing and typesetting industry. Lorem Ipsum has been the industry's text of the printing..</p>
    <a class="more">KNOW MORE...&raquo;</a>
  </article>
  <article class="card" style="left:434px">
    <div class="card-photo" role="img" aria-label="Office worker at a computer workstation"></div>
    <h3>QUORVANE SERVICES</h3>
    <div class="date"><svg width="16" height="16" viewBox="0 0 16 16"><rect x="1" y="3" width="14" height="12" fill="none" stroke="#0c5590" stroke-width="2"/><path d="M1 7h14" stroke="#0c5590" stroke-width="2"/></svg>14 Nov 2016</div>
    <p>Lorem Ipsum is simply dummy text of the print ing and typesetting industry. Lorem Ipsum has been the industry's text of the printing..</p>
    <a class="more">KNOW MORE...&raquo;</a>
  </article>
  <article class="card" style="left:790px">
    <div class="card-photo" role="img" aria-label="Team working at monitors in an operations centre"></div>
    <h3>QUORVANE SERVICES</h3>
    <div class="date"><svg width="16" height="16" viewBox="0 0 16 16"><rect x="1" y="3" width="14" height="12" fill="none" stroke="#0c5590" stroke-width="2"/><path d="M1 7h14" stroke="#0c5590" stroke-width="2"/></svg>14 Nov 2016</div>
    <p>Lorem Ipsum is simply dummy text of the print ing and typesetting industry. Lorem Ipsum has been the industry's text of the printing..</p>
    <a class="more">KNOW MORE...&raquo;</a>
  </article>
</section>

<section class="cta">
  <h2>PASSIONATE ABOUT ENGAGING WITH CLIENTS AND GROWING BUSINESS ?</h2>
  <p>Lorem Ipsum is simply dummy text of the printing and typesetting industry. Lorem Ipsum has been the industry's standard dummy text ever since the 1500s, when an unknown printer took a galley of type and scrambled it to make a type specimen book. It has survived not only five centuries, but also the leap into electronic typesetting, remaining essentially unchanged.</p>
  <a class="btn">APPLY KNOW</a>
</section>

<footer class="site-footer">
  <div class="col" style="left:78px">
    <div class="brand"><span class="brand-mark"></span>Quorvane</div>
    <p style="margin-top:30px">Lorem Ipsum is simply dummy text of the print ing and typesetting industry. Lorem Ipsum has been the.</p>
    <div class="socials"><span></span><span></span><span></span></div>
  </div>
  <div class="col" style="left:345px">
    <h4>USEFULL LINKS</h4>
    <ul class="links"><li>Home</li><li>About</li><li>Services</li><li>Strategy</li><li>Experiency</li><li>Security</li><li>News</li><li>Contact</li></ul>
  </div>
  <div class="col" style="left:610px">
    <h4>GET IN TOUCH</h4>
    <div class="contact-item"><svg width="20" height="18" viewBox="0 0 20 18"><path d="M1 3l6-2 6 2 6-2v14l-6 2-6-2-6 2z" fill="none" stroke="#6fa7d4" stroke-width="1.5"/></svg><span>101- Lorem ipsum is simple dummy text of print and type setting industry</span></div>
    <div class="contact-item"><svg width="20" height="18" viewBox="0 0 20 18"><path d="M3 1h4l2 5-3 2q2 4 6 6l2-3 5 2v4q-10 1-16-10z" fill="none" stroke="#6fa7d4" stroke-width="1.5"/></svg><span>123 456 7890</span></div>
    <div class="contact-item"><svg width="20" height="18" viewBox="0 0 20 18"><rect x="1" y="3" width="18" height="12" fill="none" stroke="#6fa7d4" stroke-width="1.5"/><path d="M1 3l9 7 9-7" fill="none" stroke="#6fa7d4" stroke-width="1.5"/></svg><span>info@quorvaneservices.com</span></div>
  </div>
  <div class="col signup" style="left:875px">
    <h4>NEWSLETTER</h4>
    <p>Would you like to receive exclusive access to articles, white papers and our regular monthly newsletter?</p>
    <input type="text" placeholder="Enter Email id">
    <a class="btn">SUBMIT</a>
  </div>
</footer>

<div class="copyright abs" style="left:0;width:1200px">&copy; <b>QUORVANE SERVICES</b> - 2016 All rights reserved.</div>

</body>
</html>
```